Fun A1 2012 family planner using clever typography and block colour

I have been looking for an A1 2012 family planner and I have not been able to find one. Hence I would like help to develop such a planner. I plan to print it on matt paper, portrait orientated. I have attached some reference pictures of our 2011 planner. I like interesting typography, clear clean colours and simple illustration. I need space to write in daily events and need the weeks and days to be clearly delineated from each other. Each day cell needs the date and day in it (please refer to the file uploaded for a visual reference confirming this). Each weekend needs some kind of colour/ typographic delineation. I want a design for a year-at-a-view calendar. I plan to print the planner in Sydney, Australia with brightloomprints.com.au and probably to sell printed copies online. The terms & conditions of this project are that I will own the design concept 100% and in perpetuity worldwide once payment has been made. (NB. The attached Work File in Word contains a rough layout and all months, days and dates all typed up to make for quicker design.)

Target Market(s)

Reasonably well heeled family of 4. 2 parents. 2 kids. 2 pets.

Industry/Entity Type

Events

Requirements
Must have
• The calendar must be portrait (not landscape orientated), A1 size. It will be printed on matt paper by brightloomprints.com.au. It must have months running left to right (Jan-Dec) and day/date cells running top to bottom (refer 2011 planner photos in file uploaded). The day/ date cells must be around 3(w)x2(h)cm - big enough to write daily events in. Weekends must be colour/ typographically delineated. 2012 year must be noted as must "A Pebblegate Inc Project" and web address in fine print bottom left hand left hand corner.
Nice to have
• A Pebblegate Inc logo in bottom left hand corder (perhaps Nimble Owl like: http://www.artmarketly.com/design_submission.aspx?designid=731462). Header/Footer space for customisation (e.g. "Hartono-Quist 2012 Planner" or "XYZ Co 2012 Planner".
Should not have
• The calendar should not use photographs or resemble standard or cheesy wall calendars. No watermarks please.

```html
<!DOCTYPE html>
<html lang="en">
<head>
<meta charset="utf-8">
<title>2012 Year Planner</title>
<link href="https://fonts.googleapis.com/css2?family=Lobster&family=Oswald:wght@300;400&display=swap" rel="stylesheet">
<style>
:root{
  --paper:#f4f4f4;
  --ink:#555;
  --ink-dark:#333;
  --rule:#c9c9c9;
  --jan:#f7a632;--feb:#ec6b2d;--mar:#cddc22;--apr:#8cc63f;
  --may:#3db54a;--jun:#0f9447;--jul:#00aeef;--aug:#1b75bc;
  --sep:#ec008c;--oct:#ee3a36;--nov:#f15a2a;--dec:#f7941e;
  --accent:#d5e022;
}
*{margin:0;padding:0;box-sizing:border-box}
html,body{width:847px;height:1200px;overflow:hidden}
body{background:var(--paper);position:relative;font-family:"Oswald",sans-serif;color:var(--ink)}
.year-grid{position:absolute;left:32px;top:64px;display:flex}
.month{width:64.6px;list-style:none}
.month-tab{width:60px;height:60px;background:var(--c);display:flex;align-items:center;justify-content:center;overflow:hidden;margin-bottom:25px}
.month-tab span{font-family:"Lobster",cursive;font-size:30px;color:#fff;transform:rotate(-58deg);text-shadow:2px 2px 0 #222,-1px -1px 0 #222,1px -1px 0 #222,-1px 1px 0 #222;line-height:1}
.days{list-style:none}
.day{height:28.6px;position:relative}
.day b,.day i{position:absolute;left:24px;width:19px;text-align:center;font-style:normal}
.day b{top:3px;font-weight:300;font-size:11px;line-height:12px}
.day i{top:15px;font-size:6px;line-height:8px;font-weight:300}
.day.we::before{content:"";position:absolute;left:24px;top:1px;width:19px;height:25px;background:var(--c)}
.day.we b,.day.we i{color:#fff}
.rules{position:absolute;left:34px;top:177.6px;width:775px;height:859px;background:repeating-linear-gradient(to bottom,var(--rule) 0 1px,transparent 1px 28.6px)}
.footer-note{position:absolute;left:37px;top:1092px;display:flex;align-items:flex-start;gap:10px}
.footer-mark{width:14px;height:14px;background:var(--accent);margin-top:6px}
.footer-year{font-family:"Oswald",sans-serif;font-weight:400;font-size:22px;line-height:26px;color:var(--ink-dark)}
.footer-credit{font-family:"Oswald",sans-serif;font-weight:300;font-size:11px;line-height:14px;color:var(--ink)}
</style>
</head>
<body>
<div class="rules"></div>
<div class="year-grid">
<div class="month" style="--c:var(--jan)"><div class="month-tab"><span>Jan</span></div><ul class="days">
<li class="day we"><b>01</b><i>SUN</i></li><li class="day"><b>02</b><i>MON</i></li><li class="day"><b>03</b><i>TUE</i></li><li class="day"><b>04</b><i>WED</i></li><li class="day"><b>05</b><i>THU</i></li><li class="day"><b>06</b><i>FRI</i></li><li class="day we"><b>07</b><i>SAT</i></li><li class="day we"><b>08</b><i>SUN</i></li><li class="day"><b>09</b><i>MON</i></li><li class="day"><b>10</b><i>TUE</i></li><li class="day"><b>11</b><i>WED</i></li><li class="day"><b>12</b><i>THU</i></li><li class="day"><b>13</b><i>FRI</i></li><li class="day we"><b>14</b><i>SAT</i></li><li class="day we"><b>15</b><i>SUN</i></li><li class="day"><b>16</b><i>MON</i></li><li class="day"><b>17</b><i>TUE</i></li><li class="day"><b>18</b><i>WED</i></li><li class="day"><b>19</b><i>THU</i></li><li class="day"><b>20</b><i>FRI</i></li><li class="day we"><b>21</b><i>SAT</i></li><li class="day we"><b>22</b><i>SUN</i></li><li class="day"><b>23</b><i>MON</i></li><li class="day"><b>24</b><i>TUE</i></li><li class="day"><b>25</b><i>WED</i></li><li class="day"><b>26</b><i>THU</i></li><li class="day"><b>27</b><i>FRI</i></li><li class="day we"><b>28</b><i>SAT</i></li><li class="day we"><b>29</b><i>SUN</i></li><li class="day"><b>30</b><i>MON</i></li><li class="day"><b>31</b><i>TUE</i></li></ul></div>
<div class="month" style="--c:var(--feb)"><div class="month-tab"><span>Feb</span></div><ul class="days">
<li class="day"><b>01</b><i>WED</i></li><li class="day"><b>02</b><i>THU</i></li><li class="day"><b>03</b><i>FRI</i></li><li class="day we"><b>04</b><i>SAT</i></li><li class="day we"><b>05</b><i>SUN</i></li><li class="day"><b>06</b><i>MON</i></li><li class="day"><b>07</b><i>TUE</i></li><li class="day"><b>08</b><i>WED</i></li><li class="day"><b>09</b><i>THU</i></li><li class="day"><b>10</b><i>FRI</i></li><li class="day we"><b>11</b><i>SAT</i></li><li class="day we"><b>12</b><i>SUN</i></li><li class="day"><b>13</b><i>MON</i></li><li class="day"><b>14</b><i>TUE</i></li><li class="day"><b>15</b><i>WED</i></li><li class="day"><b>16</b><i>THU</i></li><li class="day"><b>17</b><i>FRI</i></li><li class="day we"><b>18</b><i>SAT</i></li><li class="day we"><b>19</b><i>SUN</i></li><li class="day"><b>20</b><i>MON</i></li><li class="day"><b>21</b><i>TUE</i></li><li class="day"><b>22</b><i>WED</i></li><li class="day"><b>23</b><i>THU</i></li><li class="day"><b>24</b><i>FRI</i></li><li class="day we"><b>25</b><i>SAT</i></li><li class="day we"><b>26</b><i>SUN</i></li><li class="day"><b>27</b><i>MON</i></li><li class="day"><b>28</b><i>TUE</i></li><li class="day"><b>29</b><i>WED</i></li></ul></div>
<div class="month" style="--c:var(--mar)"><div class="month-tab"><span>Mar</span></div><ul class="days">
<li class="day"><b>01</b><i>THU</i></li><li class="day"><b>02</b><i>FRI</i></li><li class="day we"><b>03</b><i>SAT</i></li><li class="day we"><b>04</b><i>SUN</i></li><li class="day"><b>05</b><i>MON</i></li><li class="day"><b>06</b><i>TUE</i></li><li class="day"><b>07</b><i>WED</i></li><li class="day"><b>08</b><i>THU</i></li><li class="day"><b>09</b><i>FRI</i></li><li class="day we"><b>10</b><i>SAT</i></li><li class="day we"><b>11</b><i>SUN</i></li><li class="day"><b>12</b><i>MON</i></li><li class="day"><b>13</b><i>TUE</i></li><li class="day"><b>14</b><i>WED</i></li><li class="day"><b>15</b><i>THU</i></li><li class="day"><b>16</b><i>FRI</i></li><li class="day we"><b>17</b><i>SAT</i></li><li class="day we"><b>18</b><i>SUN</i></li><li class="day"><b>19</b><i>MON</i></li><li class="day"><b>20</b><i>TUE</i></li><li class="day"><b>21</b><i>WED</i></li><li class="day"><b>22</b><i>THU</i></li><li class="day"><b>23</b><i>FRI</i></li><li class="day we"><b>24</b><i>SAT</i></li><li class="day we"><b>25</b><i>SUN</i></li><li class="day"><b>26</b><i>MON</i></li><li class="day"><b>27</b><i>TUE</i></li><li class="day"><b>28</b><i>WED</i></li><li class="day"><b>29</b><i>THU</i></li><li class="day"><b>30</b><i>FRI</i></li><li class="day we"><b>31</b><i>SAT</i></li></ul></div>
<div class="month" style="--c:var(--apr)"><div class="month-tab"><span>Apr</span></div><ul class="days">
<li class="day we"><b>01</b><i>SUN</i></li><li class="day"><b>02</b><i>MON</i></li><li class="day"><b>03</b><i>TUE</i></li><li class="day"><b>04</b><i>WED</i></li><li class="day"><b>05</b><i>THU</i></li><li class="day"><b>06</b><i>FRI</i></li><li class="day we"><b>07</b><i>SAT</i></li><li class="day we"><b>08</b><i>SUN</i></li><li class="day"><b>09</b><i>MON</i></li><li class="day"><b>10</b><i>TUE</i></li><li class="day"><b>11</b><i>WED</i></li><li class="day"><b>12</b><i>THU</i></li><li class="day"><b>13</b><i>FRI</i></li><li class="day we"><b>14</b><i>SAT</i></li><li class="day we"><b>15</b><i>SUN</i></li><li class="day"><b>16</b><i>MON</i></li><li class="day"><b>17</b><i>TUE</i></li><li class="day"><b>18</b><i>WED</i></li><li class="day"><b>19</b><i>THU</i></li><li class="day"><b>20</b><i>FRI</i></li><li class="day we"><b>21</b><i>SAT</i></li><li class="day we"><b>22</b><i>SUN</i></li><li class="day"><b>23</b><i>MON</i></li><li class="day"><b>24</b><i>TUE</i></li><li class="day"><b>25</b><i>WED</i></li><li class="day"><b>26</b><i>THU</i></li><li class="day"><b>27</b><i>FRI</i></li><li class="day we"><b>28</b><i>SAT</i></li><li class="day we"><b>29</b><i>SUN</i></li><li class="day"><b>30</b><i>MON</i></li></ul></div>
<div class="month" style="--c:var(--may)"><div class="month-tab"><span>May</span></div><ul class="days">
<li class="day"><b>01</b><i>TUE</i></li><li class="day"><b>02</b><i>WED</i></li><li class="day"><b>03</b><i>THU</i></li><li class="day"><b>04</b><i>FRI</i></li><li class="day we"><b>05</b><i>SAT</i></li><li class="day we"><b>06</b><i>SUN</i></li><li class="day"><b>07</b><i>MON</i></li><li class="day"><b>08</b><i>TUE</i></li><li class="day"><b>09</b><i>WED</i></li><li class="day"><b>10</b><i>THU</i></li><li class="day"><b>11</b><i>FRI</i></li><li class="day we"><b>12</b><i>SAT</i></li><li class="day we"><b>13</b><i>SUN</i></li><li class="day"><b>14</b><i>MON</i></li><li class="day"><b>15</b><i>TUE</i></li><li class="day"><b>16</b><i>WED</i></li><li class="day"><b>17</b><i>THU</i></li><li class="day"><b>18</b><i>FRI</i></li><li class="day we"><b>19</b><i>SAT</i></li><li class="day we"><b>20</b><i>SUN</i></li><li class="day"><b>21</b><i>MON</i></li><li class="day"><b>22</b><i>TUE</i></li><li class="day"><b>23</b><i>WED</i></li><li class="day"><b>24</b><i>THU</i></li><li class="day"><b>25</b><i>FRI</i></li><li class="day we"><b>26</b><i>SAT</i></li><li class="day we"><b>27</b><i>SUN</i></li><li class="day"><b>28</b><i>MON</i></li><li class="day"><b>29</b><i>TUE</i></li><li class="day"><b>30</b><i>WED</i></li><li class="day"><b>31</b><i>THU</i></li></ul></div>
<div class="month" style="--c:var(--jun)"><div class="month-tab"><span>Jun</span></div><ul class="days">
<li class="day"><b>01</b><i>FRI</i></li><li class="day we"><b>02</b><i>SAT</i></li><li class="day we"><b>03</b><i>SUN</i></li><li class="day"><b>04</b><i>MON</i></li><li class="day"><b>05</b><i>TUE</i></li><li class="day"><b>06</b><i>WED</i></li><li class="day"><b>07</b><i>THU</i></li><li class="day"><b>08</b><i>FRI</i></li><li class="day we"><b>09</b><i>SAT</i></li><li class="day we"><b>10</b><i>SUN</i></li><li class="day"><b>11</b><i>MON</i></li><li class="day"><b>12</b><i>TUE</i></li><li class="day"><b>13</b><i>WED</i></li><li class="day"><b>14</b><i>THU</i></li><li class="day"><b>15</b><i>FRI</i></li><li class="day we"><b>16</b><i>SAT</i></li><li class="day we"><b>17</b><i>SUN</i></li><li class="day"><b>18</b><i>MON</i></li><li class="day"><b>19</b><i>TUE</i></li><li class="day"><b>20</b><i>WED</i></li><li class="day"><b>21</b><i>THU</i></li><li class="day"><b>22</b><i>FRI</i></li><li class="day we"><b>23</b><i>SAT</i></li><li class="day we"><b>24</b><i>SUN</i></li><li class="day"><b>25</b><i>MON</i></li><li class="day"><b>26</b><i>TUE</i></li><li class="day"><b>27</b><i>WED</i></li><li class="day"><b>28</b><i>THU</i></li><li class="day"><b>29</b><i>FRI</i></li><li class="day we"><b>30</b><i>SAT</i></li></ul></div>
<div class="month" style="--c:var(--jul)"><div class="month-tab"><span>Jul</span></div><ul class="days">
<li class="day we"><b>01</b><i>SUN</i></li><li class="day"><b>02</b><i>MON</i></li><li class="day"><b>03</b><i>TUE</i></li><li class="day"><b>04</b><i>WED</i></li><li class="day"><b>05</b><i>THU</i></li><li class="day"><b>06</b><i>FRI</i></li><li class="day we"><b>07</b><i>SAT</i></li><li class="day we"><b>08</b><i>SUN</i></li><li class="day"><b>09</b><i>MON</i></li><li class="day"><b>10</b><i>TUE</i></li><li class="day"><b>11</b><i>WED</i></li><li class="day"><b>12</b><i>THU</i></li><li class="day"><b>13</b><i>FRI</i></li><li class="day we"><b>14</b><i>SAT</i></li><li class="day we"><b>15</b><i>SUN</i></li><li class="day"><b>16</b><i>MON</i></li><li class="day"><b>17</b><i>TUE</i></li><li class="day"><b>18</b><i>WED</i></li><li class="day"><b>19</b><i>THU</i></li><li class="day"><b>20</b><i>FRI</i></li><li class="day we"><b>21</b><i>SAT</i></li><li class="day we"><b>22</b><i>SUN</i></li><li class="day"><b>23</b><i>MON</i></li><li class="day"><b>24</b><i>TUE</i></li><li class="day"><b>25</b><i>WED</i></li><li class="day"><b>26</b><i>THU</i></li><li class="day"><b>27</b><i>FRI</i></li><li class="day we"><b>28</b><i>SAT</i></li><li class="day we"><b>29</b><i>SUN</i></li><li class="day"><b>30</b><i>MON</i></li><li class="day"><b>31</b><i>TUE</i></li></ul></div>
<div class="month" style="--c:var(--aug)"><div class="month-tab"><span>Aug</span></div><ul class="days">
<li class="day"><b>01</b><i>WED</i></li><li class="day"><b>02</b><i>THU</i></li><li class="day"><b>03</b><i>FRI</i></li><li class="day we"><b>04</b><i>SAT</i></li><li class="day we"><b>05</b><i>SUN</i></li><li class="day"><b>06</b><i>MON</i></li><li class="day"><b>07</b><i>TUE</i></li><li class="day"><b>08</b><i>WED</i></li><li class="day"><b>09</b><i>THU</i></li><li class="day"><b>10</b><i>FRI</i></li><li class="day we"><b>11</b><i>SAT</i></li><li class="day we"><b>12</b><i>SUN</i></li><li class="day"><b>13</b><i>MON</i></li><li class="day"><b>14</b><i>TUE</i></li><li class="day"><b>15</b><i>WED</i></li><li class="day"><b>16</b><i>THU</i></li><li class="day"><b>17</b><i>FRI</i></li><li class="day we"><b>18</b><i>SAT</i></li><li class="day we"><b>19</b><i>SUN</i></li><li class="day"><b>20</b><i>MON</i></li><li class="day"><b>21</b><i>TUE</i></li><li class="day"><b>22</b><i>WED</i></li><li class="day"><b>23</b><i>THU</i></li><li class="day"><b>24</b><i>FRI</i></li><li class="day we"><b>25</b><i>SAT</i></li><li class="day we"><b>26</b><i>SUN</i></li><li class="day"><b>27</b><i>MON</i></li><li class="day"><b>28</b><i>TUE</i></li><li class="day"><b>29</b><i>WED</i></li><li class="day"><b>30</b><i>THU</i></li><li class="day"><b>31</b><i>FRI</i></li></ul></div>
<div class="month" style="--c:var(--sep)"><div class="month-tab"><span>Sep</span></div><ul class="days">
<li class="day we"><b>01</b><i>SAT</i></li><li class="day we"><b>02</b><i>SUN</i></li><li class="day"><b>03</b><i>MON</i></li><li class="day"><b>04</b><i>TUE</i></li><li class="day"><b>05</b><i>WED</i></li><li class="day"><b>06</b><i>THU</i></li><li class="day"><b>07</b><i>FRI</i></li><li class="day we"><b>08</b><i>SAT</i></li><li class="day we"><b>09</b><i>SUN</i></li><li class="day"><b>10</b><i>MON</i></li><li class="day"><b>11</b><i>TUE</i></li><li class="day"><b>12</b><i>WED</i></li><li class="day"><b>13</b><i>THU</i></li><li class="day"><b>14</b><i>FRI</i></li><li class="day we"><b>15</b><i>SAT</i></li><li class="day we"><b>16</b><i>SUN</i></li><li class="day"><b>17</b><i>MON</i></li><li class="day"><b>18</b><i>TUE</i></li><li class="day"><b>19</b><i>WED</i></li><li class="day"><b>20</b><i>THU</i></li><li class="day"><b>21</b><i>FRI</i></li><li class="day we"><b>22</b><i>SAT</i></li><li class="day we"><b>23</b><i>SUN</i></li><li class="day"><b>24</b><i>MON</i></li><li class="day"><b>25</b><i>TUE</i></li><li class="day"><b>26</b><i>WED</i></li><li class="day"><b>27</b><i>THU</i></li><li class="day"><b>28</b><i>FRI</i></li><li class="day we"><b>29</b><i>SAT</i></li><li class="day we"><b>30</b><i>SUN</i></li></ul></div>
<div class="month" style="--c:var(--oct)"><div class="month-tab"><span>Oct</span></div><ul class="days">
<li class="day"><b>01</b><i>MON</i></li><li class="day"><b>02</b><i>TUE</i></li><li class="day"><b>03</b><i>WED</i></li><li class="day"><b>04</b><i>THU</i></li><li class="day"><b>05</b><i>FRI</i></li><li class="day we"><b>06</b><i>SAT</i></li><li class="day we"><b>07</b><i>SUN</i></li><li class="day"><b>08</b><i>MON</i></li><li class="day"><b>09</b><i>TUE</i></li><li class="day"><b>10</b><i>WED</i></li><li class="day"><b>11</b><i>THU</i></li><li class="day"><b>12</b><i>FRI</i></li><li class="day we"><b>13</b><i>SAT</i></li><li class="day we"><b>14</b><i>SUN</i></li><li class="day"><b>15</b><i>MON</i></li><li class="day"><b>16</b><i>TUE</i></li><li class="day"><b>17</b><i>WED</i></li><li class="day"><b>18</b><i>THU</i></li><li class="day"><b>19</b><i>FRI</i></li><li class="day we"><b>20</b><i>SAT</i></li><li class="day we"><b>21</b><i>SUN</i></li><li class="day"><b>22</b><i>MON</i></li><li class="day"><b>23</b><i>TUE</i></li><li class="day"><b>24</b><i>WED</i></li><li class="day"><b>25</b><i>THU</i></li><li class="day"><b>26</b><i>FRI</i></li><li class="day we"><b>27</b><i>SAT</i></li><li class="day we"><b>28</b><i>SUN</i></li><li class="day"><b>29</b><i>MON</i></li><li class="day"><b>30</b><i>TUE</i></li><li class="day"><b>31</b><i>WED</i></li></ul></div>
<div class="month" style="--c:var(--nov)"><div class="month-tab"><span>Nov</span></div><ul class="days">
<li class="day"><b>01</b><i>THU</i></li><li class="day"><b>02</b><i>FRI</i></li><li class="day we"><b>03</b><i>SAT</i></li><li class="day we"><b>04</b><i>SUN</i></li><li class="day"><b>05</b><i>MON</i></li><li class="day"><b>06</b><i>TUE</i></li><li class="day"><b>07</b><i>WED</i></li><li class="day"><b>08</b><i>THU</i></li><li class="day"><b>09</b><i>FRI</i></li><li class="day we"><b>10</b><i>SAT</i></li><li class="day we"><b>11</b><i>SUN</i></li><li class="day"><b>12</b><i>MON</i></li><li class="day"><b>13</b><i>TUE</i></li><li class="day"><b>14</b><i>WED</i></li><li class="day"><b>15</b><i>THU</i></li><li class="day"><b>16</b><i>FRI</i></li><li class="day we"><b>17</b><i>SAT</i></li><li class="day we"><b>18</b><i>SUN</i></li><li class="day"><b>19</b><i>MON</i></li><li class="day"><b>20</b><i>TUE</i></li><li class="day"><b>21</b><i>WED</i></li><li class="day"><b>22</b><i>THU</i></li><li class="day"><b>23</b><i>FRI</i></li><li class="day we"><b>24</b><i>SAT</i></li><li class="day we"><b>25</b><i>SUN</i></li><li class="day"><b>26</b><i>MON</i></li><li class="day"><b>27</b><i>TUE</i></li><li class="day"><b>28</b><i>WED</i></li><li class="day"><b>29</b><i>THU</i></li><li class="day"><b>30</b><i>FRI</i></li></ul></div>
<div class="month" style="--c:var(--dec)"><div class="month-tab"><span>Dec</span></div><ul class="days">
<li class="day we"><b>01</b><i>SAT</i></li><li class="day we"><b>02</b><i>SUN</i></li><li class="day"><b>03</b><i>MON</i></li><li class="day"><b>04</b><i>TUE</i></li><li class="day"><b>05</b><i>WED</i></li><li class="day"><b>06</b><i>THU</i></li><li class="day"><b>07</b><i>FRI</i></li><li class="day we"><b>08</b><i>SAT</i></li><li class="day we"><b>09</b><i>SUN</i></li><li class="day"><b>10</b><i>MON</i></li><li class="day"><b>11</b><i>TUE</i></li><li class="day"><b>12</b><i>WED</i></li><li class="day"><b>13</b><i>THU</i></li><li class="day"><b>14</b><i>FRI</i></li><li class="day we"><b>15</b><i>SAT</i></li><li class="day we"><b>16</b><i>SUN</i></li><li class="day"><b>17</b><i>MON</i></li><li class="day"><b>18</b><i>TUE</i></li><li class="day"><b>19</b><i>WED</i></li><li class="day"><b>20</b><i>THU</i></li><li class="day"><b>21</b><i>FRI</i></li><li class="day we"><b>22</b><i>SAT</i></li><li class="day we"><b>23</b><i>SUN</i></li><li class="day"><b>24</b><i>MON</i></li><li class="day"><b>25</b><i>TUE</i></li><li class="day"><b>26</b><i>WED</i></li><li class="day"><b>27</b><i>THU</i></li><li class="day"><b>28</b><i>FRI</i></li><li class="day we"><b>29</b><i>SAT</i></li><li class="day we"><b>30</b><i>SUN</i></li><li class="day"><b>31</b><i>MON</i></li></ul></div>
</div>
<div class="footer-note">
  <div class="footer-mark"></div>
  <div>
    <div class="footer-year">2012</div>
    <div class="footer-credit">A Pebblegate Inc Project</div>
  </div>
</div>
</body>
</html>
```